Road Construction Company needs business cards

We would like a new business card designed for our business.

We're a road construction company based in Qld, Australia.

Can the business card please have the following information on it.

Name: Warren Halbeck
Position: General Manager
Phone: 0472 915 348
Email: Warren.halbeck@tovrin.com.au
Address: 87 Marrow Ave, Pendlebay, QLD, 4023
Website: www.tovrin.com.au

Visually we'd like the card to be professional and simple.

Attached is our logo.

Our website is www.tovrin.com.au

Target Market(s)

Men aged 25-60

Contact Information for Business Card

As listed in project description

Font styles to use
Serif

Requirements
Must have
• Large logo on back of card

```html
<!DOCTYPE html>
<html lang="en">
<head>
<meta charset="utf-8">
<title>Tovrin Business Card</title>
<link href="https://fonts.googleapis.com/css2?family=Arimo:wght@400;700&family=Source+Sans+3:wght@300&display=swap" rel="stylesheet">
<style>
  :root {
    --navy: #0b4fa3;
    --sky: #34a7da;
    --lavender: #c9cce7;
    --paper: #ffffff;
    --backdrop: #ececec;
  }
  * { margin: 0; padding: 0; box-sizing: border-box; }
  html, body {
    width: 1200px; height: 1000px; overflow: hidden;
    background: var(--backdrop);
    font-family: "Arimo", Arial, sans-serif;
  }
  .card {
    position: absolute;
    left: 260px;
    width: 680px; height: 388px;
    background: var(--paper);
    overflow: hidden;
  }
  .card--front { top: 78px; }
  .card--back { top: 539px; }
  .card-shapes { position: absolute; inset: 0; }

  .brand-name {
    position: absolute;
    font-family: "Arimo", Arial, sans-serif;
    font-weight: 700;
    color: var(--navy);
    letter-spacing: 0.04em;
    line-height: 1;
  }
  .card--front .brand-name { left: 47px; top: 126px; font-size: 44px; }
  .card--back .brand-name {
    left: 0; right: 0; top: 142px;
    text-align: center; font-size: 92px;
  }

  .holder { position: absolute; left: 40px; top: 266px; color: #fff; }
  .holder-name { font-size: 32px; font-weight: 400; line-height: 1; letter-spacing: 0.01em; }
  .holder-role {
    margin-top: 10px;
    font-family: "Source Sans 3", sans-serif;
    font-weight: 300; font-size: 27px; line-height: 1;
  }

  .contact-list { position: absolute; left: 359px; top: 0; list-style: none; }
  .contact-item { position: absolute; display: flex; align-items: center; left: 0; white-space: nowrap; }
  .contact-badge {
    width: 28px; height: 28px; border-radius: 50%;
    background: var(--sky); color: #fff;
    font-size: 16px; line-height: 28px; text-align: center;
    flex: none;
  }
  .contact-text {
    margin-left: 40px;
    color: var(--navy);
    font-size: 16px; line-height: 19px;
  }
  .contact-item--phone { top: 57px; }
  .contact-item--email { top: 105px; }
  .contact-item--address { top: 151px; }
  .contact-item--web { top: 200px; }

  .back-web {
    position: absolute; left: 0; right: 0; top: 337px;
    text-align: center; color: var(--navy); font-size: 16px;
  }
</style>
</head>
<body>

<section class="card card--front" aria-label="Business card front">
  <svg class="card-shapes" width="680" height="388" viewBox="0 0 680 388" aria-hidden="true">
    <circle cx="657" cy="-43" r="128" fill="var(--lavender)"/>
    <circle cx="14" cy="379" r="159" fill="var(--lavender)"/>
    <path d="M0 255 H303 C345 255 368 273 388 298 L424 357 H0 Z" fill="var(--sky)"/>
    <rect x="420" y="354" width="260" height="2.5" fill="var(--sky)"/>
  </svg>

  <div class="brand-name">TOVRIN</div>

  <div class="holder">
    <p class="holder-name">WARREN HALBECK</p>
    <p class="holder-role">General Manager</p>
  </div>

  <ul class="contact-list">
    <li class="contact-item contact-item--phone"><span class="contact-badge">P</span><span class="contact-text">0472 915 348</span></li>
    <li class="contact-item contact-item--email"><span class="contact-badge">E</span><span class="contact-text">Warren.halbeck@tovrin.com.au</span></li>
    <li class="contact-item contact-item--address"><span class="contact-badge">A</span><span class="contact-text">87 Marrow Ave, Pendlebay,<br>QLD, 4023</span></li>
    <li class="contact-item contact-item--web"><span class="contact-badge">W</span><span class="contact-text">www.tovrin.com.au</span></li>
  </ul>
</section>

<section class="card card--back" aria-label="Business card back">
  <svg class="card-shapes" width="680" height="388" viewBox="0 0 680 388" aria-hidden="true">
    <circle cx="82" cy="-25" r="129" fill="var(--lavender)"/>
    <circle cx="637" cy="387" r="136" fill="var(--lavender)"/>
  </svg>
  <div class="brand-name">TOVRIN</div>
  <p class="back-web">www.tovrin.com.au</p>
</section>

</body>
</html>
```